Lumen Fitness Personal Training Business

I need a business card design with a logo for my personal training company. I'd like the colors to be a vibrant green and black. I'd like the logo to incorporate an anvil (or something similar). I train hardcore competitive athletes as well as soccer moms trying to get and/or stay in shape. I need a logo that will not pigeon hole me in one category or the other, but at the same time not be too intimidating to soccer moms, but will not be off putting to the more hardcore trainees. The design should be attention grabbing and aesthetic.
Target Market(s)
Hardcore athletes as well as average people just trying to get/stay in shape.
Industry/Entity Type
Training

```html
<!DOCTYPE html>
<html lang="en">
<head>
<meta charset="utf-8">
<title>Lumen Fitness Business Card</title>
<link rel="stylesheet" href="https://fonts.googleapis.com/css2?family=Open+Sans:wght@400;600;700&display=swap">
<style>
  :root {
    --page-bg: #d9d9d9;
    --card-white: #f8f9f7;
    --ink-black: #141414;
    --vibrant-green: #3dbb2f;
    --light-green: #6fdc4f;
    --title-grey: #6b6e6a;
    --text-white: #ffffff;
  }
  * { box-sizing: border-box; margin: 0; padding: 0; }
  html, body {
    width: 1200px; height: 900px; overflow: hidden;
    background: var(--page-bg);
    font-family: "Open Sans", sans-serif;
  }
  .card {
    position: absolute; left: 250px; width: 700px; height: 400px;
    overflow: hidden; box-shadow: 0 6px 18px rgba(0,0,0,.18);
  }

  /* Back side */
  .card-back { top: 40px; background: var(--ink-black); }
  .card-back .brand-mark {
    position: absolute; top: 150px; left: 0; right: 0;
    display: flex; align-items: center; justify-content: center; gap: 16px;
  }
  .card-back .brand-dot { width: 30px; height: 30px; border-radius: 50%; background: var(--vibrant-green); }
  .card-back .brand-name {
    font-weight: 700; font-size: 52px; letter-spacing: 3px; line-height: 1;
    color: var(--vibrant-green);
  }
  .card-back .edge-stripe {
    position: absolute; left: 0; right: 0; bottom: 46px; height: 12px; background: var(--vibrant-green);
  }

  /* Front side */
  .card-front { top: 470px; background: var(--card-white); }
  .card-front .brand-mark {
    position: absolute; top: 62px; left: 44px;
    display: flex; align-items: center; gap: 12px;
  }
  .card-front .brand-dot { width: 22px; height: 22px; border-radius: 50%; background: var(--vibrant-green); }
  .card-front .brand-name {
    font-weight: 700; font-size: 34px; letter-spacing: 2px; line-height: 1;
    color: var(--vibrant-green);
  }
  .person {
    position: absolute; top: 128px; right: 48px; text-align: right;
  }
  .person-name { font-weight: 700; font-size: 21px; letter-spacing: .5px; color: var(--ink-black); }
  .person-title { font-weight: 400; font-size: 17px; color: var(--title-grey); margin-top: 2px; }

  .contact-band {
    position: absolute; left: 0; right: 0; bottom: 0; height: 175px; background: var(--ink-black);
  }
  .contact-band .band-stripe {
    position: absolute; left: 0; right: 0; bottom: 34px; height: 13px; background: var(--vibrant-green);
  }
  .contact-columns {
    position: absolute; left: 0; right: 0; top: 30px;
    display: flex; justify-content: space-between; padding: 0 44px;
    color: var(--text-white); font-size: 15px; line-height: 1.6;
  }
  .contact-line { display: flex; align-items: center; gap: 7px; white-space: nowrap; }
  .contact-line.continued { padding-left: 20px; }
  .icon { width: 13px; height: 13px; fill: var(--light-green); flex: none; }
  .icon-stroke { fill: none; stroke: var(--light-green); stroke-width: 1.4; stroke-linecap: round; }
</style>
</head>
<body>

<section class="card card-back">
  <div class="brand-mark">
    <span class="brand-dot"></span>
    <span class="brand-name">LUMEN FITNESS</span>
  </div>
  <div class="edge-stripe"></div>
</section>

<section class="card card-front">
  <div class="brand-mark">
    <span class="brand-dot"></span>
    <span class="brand-name">LUMEN FITNESS</span>
  </div>

  <div class="person">
    <div class="person-name">DANIEL REYES</div>
    <div class="person-title">Managing Director</div>
  </div>

  <div class="contact-band">
    <div class="contact-columns">
      <div class="col">
        <div class="contact-line">
          <svg class="icon" viewBox="0 0 12 12"><path d="M6 0a4 4 0 0 0-4 4c0 3 4 8 4 8s4-5 4-8a4 4 0 0 0-4-4zm0 5.6A1.6 1.6 0 1 1 6 2.4a1.6 1.6 0 0 1 0 3.2z"/></svg>
          <span>1234, Address Goes Here,</span>
        </div>
        <div class="contact-line continued"><span>Country Name, 123456</span></div>
      </div>
      <div class="col">
        <div class="contact-line">
          <svg class="icon" viewBox="0 0 12 12"><path d="M1 3.5C1 2 3 1.5 6 1.5s5 .5 5 2v1H8.5V3.5h-5v1H1zM2.5 5.5h7l1 5h-9z"/></svg>
          <span>123.456.7890</span>
        </div>
        <div class="contact-line">
          <svg class="icon" viewBox="0 0 12 12"><path d="M1 4h10v7H1zM3 1h6v2.5H3zM3 6h2v1.5H3zm3 0h3v1.5H6zM3 8.5h6V10H3z"/></svg>
          <span>123.456.7890</span>
        </div>
      </div>
      <div class="col">
        <div class="contact-line">
          <svg class="icon" viewBox="0 0 12 12"><path d="M0 2.5h12v7H0zM1 3.3l5 3.6 5-3.6v-.1H1z"/></svg>
          <span>info@youremail.com</span>
        </div>
        <div class="contact-line">
          <svg class="icon" viewBox="0 0 12 12"><path class="icon-stroke" d="M4.5 7.5l3-3M5 3.5l1.5-1.5a2 2 0 0 1 3 3L8 6.5M7 8.5L5.5 10a2 2 0 0 1-3-3L4 5.5"/></svg>
          <span>www.website.com</span>
        </div>
      </div>
    </div>
    <div class="band-stripe"></div>
  </div>
</section>

</body>
</html>
```